Voltara Growth Partners in need of a business card design

We need an innovative business card designed for a new company in Alberta, Canada. We assist organizations in improving performance by providing coaching and mentorship on how to promote and achieve organizational excellence. We teach senior leaders and their staff on how to continually improve performance; assist them in making sure the organization is innovative, competitive, and customer focused; support them in making sure the culture of the organization is also healthy, inclusive, and sustainable; and they are economically, socially, and environmentally responsible. We will do this by staying true to our company values of respect, excellence, integrity and trust.

Attached is our newly designed logo.

The team thought that having an inspirational quote similar to this one below would be a good addition somewhere on the card.

"Autograph your work with excellence.''

Target Market(s)

Private and public sector organizations. Once that are interested in being a Top 100 employer.

Industry/Entity Type

Business

Font styles to use
Sans Serif

Requirements
Must have
• 1. The business card must be double-sided.
2. Person's name and title
3. Email address
4. Phone number
5. Website (voltaragrowth.ca)
6. QR code
7. A quote somewhere on the front of the card: Autograph your work with excellence.
Nice to have

```html
<!DOCTYPE html>
<html lang="en">
<head>
<meta charset="utf-8">
<title>Voltara Growth Partners – Business Card</title>
<link href="https://fonts.googleapis.com/css2?family=Didact+Gothic&family=Roboto:wght@400;700&display=swap" rel="stylesheet">
<style>
  :root {
    --page: #e8e4df;
    --card: #121214;
    --card-edge: #1d1d21;
    --white: #f4f4f4;
    --purple: #8e70c2;
    --blue: #3ea6da;
    --green: #9ccc2e;
    --rule: #55565c;
  }
  * { box-sizing: border-box; margin: 0; padding: 0; }
  html, body { width: 1200px; height: 913px; overflow: hidden; }
  body {
    background: var(--page);
    font-family: "Roboto", Arial, sans-serif;
    display: flex;
    align-items: center;
    justify-content: center;
    gap: 40px;
  }
  .card {
    width: 540px;
    height: 309px;
    background: radial-gradient(ellipse at 35% 30%, var(--card-edge), var(--card) 70%);
    border-radius: 4px;
    box-shadow: 0 6px 18px rgba(0,0,0,.25);
    position: relative;
    color: var(--white);
    overflow: hidden;
  }

  /* Back side: company name */
  .card--back { display: flex; align-items: center; justify-content: center; }
  .brand-mark {
    display: flex; align-items: center; gap: 16px;
  }
  .brand-mark__dot {
    width: 26px; height: 26px; border-radius: 50%; background: var(--green);
  }
  .brand-mark__name {
    font-family: "Roboto", Arial, sans-serif;
    font-weight: 700;
    font-size: 34px;
    line-height: 1.05;
    color: var(--white);
    letter-spacing: .5px;
  }

  /* Front side: contact + quote */
  .card--front { display: grid; grid-template-columns: 1fr 1px 1fr; }
  .contact { padding: 40px 0 0 30px; }
  .contact__brand {
    font-weight: 700; font-size: 21px; line-height: 1.1; color: var(--white);
    margin-bottom: 40px;
  }
  .contact__name { font-weight: 700; font-size: 17px; }
  .contact__title { font-size: 13px; margin: 3px 0 14px; }
  .contact__list { list-style: none; font-size: 12.5px; }
  .contact__list li { display: flex; align-items: center; gap: 10px; margin-bottom: 5px; }
  .contact__list svg { width: 15px; height: 15px; flex: none; }
  .contact__phone { color: var(--purple); }
  .contact__email { color: var(--blue); }
  .contact__web { color: var(--green); }

  .divider {
    background: linear-gradient(to bottom, transparent, var(--rule) 20%, var(--rule) 80%, transparent);
    margin: 20px 0;
  }
  .quote {
    font-family: "Didact Gothic", Arial, sans-serif;
    display: flex; flex-direction: column; justify-content: center; align-items: center;
    padding: 0 28px; text-align: center;
  }
  .quote__text { font-size: 16px; line-height: 1.75; }
  .quote__author { align-self: flex-end; color: var(--green); font-size: 13px; margin-top: 8px; }
</style>
</head>
<body>

  <section class="card card--back" aria-label="Card back">
    <div class="brand-mark">
      <span class="brand-mark__dot"></span>
      <span class="brand-mark__name">Voltara<br>Growth Partners</span>
    </div>
  </section>

  <section class="card card--front" aria-label="Card front">
    <div class="contact">
      <p class="contact__brand">Voltara<br>Growth Partners</p>
      <p class="contact__name">Your Long Name</p>
      <p class="contact__title">Titel</p>
      <ul class="contact__list">
        <li class="contact__phone">
          <svg viewBox="0 0 16 16" aria-hidden="true"><path fill="currentColor" d="M3 1.5l2.5-.5 1.5 3.5-1.8 1.2a8 8 0 0 0 4.1 4.1l1.2-1.8 3.5 1.5-.5 2.5C12 13.5 2.5 4 3 1.5z"/></svg>
          00.00.00.0000
        </li>
        <li class="contact__email">
          <svg viewBox="0 0 16 16" aria-hidden="true"><rect x="1" y="3" width="14" height="10" fill="none" stroke="currentColor" stroke-width="1.5"/><path d="M1 3l7 6 7-6" fill="none" stroke="currentColor" stroke-width="1.5"/></svg>
          yourname@yourwebsite.com
        </li>
        <li class="contact__web">
          <svg viewBox="0 0 16 16" aria-hidden="true"><g fill="none" stroke="currentColor" stroke-width="1.3"><circle cx="8" cy="8" r="6.5"/><ellipse cx="8" cy="8" rx="3" ry="6.5"/><path d="M1.5 8h13"/></g></svg>
          www.yourwebsite.com
        </li>
      </ul>
    </div>
    <div class="divider"></div>
    <blockquote class="quote">
      <p class="quote__text">Every job is a<br>self-portrait<br>of the person who<br>did it.<br>Autograph your<br>work with excellence.</p>
      <cite class="quote__author">- Anonymous</cite>
    </blockquote>
  </section>

</body>
</html>
```